Adult Literacy Program - flyer to attract volunteers and students

We want a flyer that is engaging, colorful, modern and will appeal to our primary audience of adults aged 40-60. We are trying to attract both prospective volunteers (typically age 50+, mostly women) and students (typically aged 40+).
The flyer should feature diverse people working together in pairs of two, reading or talking, with a workbook or some reading material in front of them.

Our organization trains tutors to work one-on-one with adults who are learning how to read. Most of our adult students are non-native speakers of English. Many are of Haitian or Hispanic origin, so we would like some people who represent that demographic.

The Flyer should represent reading, learning, literacy, knowledge, growth,
and opportunities.
Our students are learning to read so they can advance their job opportunities.

Target Market(s)

Adults aged 40-60, primarily women, retired, volunteers

Industry/Entity Type

Education

Font styles to use
Serif
Sans Serif

Colors

Designer to choose colors to be used in the design.

Requirements
Must have
• - UPDATE: Should be designed as a TRI-FOLD brochure on 8.5 x 11 inch paper that will be folded into thirds.
• - Images of diverse people, women and men, who look Hispanic, Haitian and other nationalities as well as Caucasian.
• - Our logo on the front cover
Nice to have
• The sample flyer is very boring and dry! We are open to different ways of presenting the text.

```html
<!DOCTYPE html>
<html lang="en">
<head>
<meta charset="utf-8">
<title>Reading Bridge Friends – Tri-fold Brochure</title>
<link rel="stylesheet" href="https://fonts.googleapis.com/css2?family=Lato:wght@400;700;900&display=swap">
<style>
  :root {
    --navy: #1b2a6b;
    --blue-light: #2aa9e0;
    --blue-mid: #1689cc;
    --blue-deep: #0d6ab0;
    --white: #ffffff;
    --page-bg: #eef0f3;
  }
  * { box-sizing: border-box; margin: 0; padding: 0; }
  html, body { width: 882px; height: 1200px; overflow: hidden; }
  body {
    background: var(--page-bg);
    font-family: "Lato", Arial, sans-serif;
    position: relative;
  }
  .spread {
    position: absolute;
    left: 21px;
    width: 840px;
    height: 560px;
    overflow: hidden;
    box-shadow: 0 4px 14px rgba(0,0,0,.18);
  }
  .spread--outside { top: 25px; }
  .spread--inside { top: 615px; }
  .spread__art { position: absolute; inset: 0; }
  .txt { position: absolute; color: var(--white); }

  /* Logo badge */
  .logo-badge {
    position: absolute;
    display: flex; align-items: center; justify-content: center;
    text-align: center;
    border-radius: 50%;
    background: var(--white);
    border: 4px solid var(--navy);
  }
  .logo-badge__name {
    font-family: "Lato", Arial, sans-serif;
    font-weight: 900;
    font-size: 14px;
    line-height: 1.15;
    color: var(--navy);
    text-transform: uppercase;
  }

  /* Outside spread */
  .cta-title { left: 305px; top: 34px; width: 250px; text-align: center;
    color: var(--navy); font-weight: 900; font-size: 29px; line-height: 1.05; }
  .cta-sub { left: 305px; top: 112px; width: 250px; text-align: center;
    font-weight: 900; font-size: 18px; line-height: 1.1; }
  .contact-line { left: 310px; width: 250px; font-size: 14px; line-height: 1.3; }
  .contact-line strong { font-weight: 900; }
  .contact-line--desk { top: 170px; }
  .contact-line--desk strong { font-size: 16px; }
  .contact-line--branches { top: 202px; }
  .contact-line--branches strong { font-size: 22px; }
  .contact-line--email { top: 280px; font-weight: 700; font-size: 13px; }

  .cover-title { left: 568px; top: 128px; width: 262px; text-align: center;
    color: var(--navy); font-weight: 900; font-size: 40px; letter-spacing: .5px; }
  .cover-tag { left: 680px; top: 178px; padding: 3px 12px; border-radius: 14px;
    background: var(--navy); font-weight: 700; font-size: 15px; }
  .cover-lede { left: 580px; top: 218px; width: 240px; text-align: center;
    font-size: 14px; line-height: 1.35; }

  /* Inside spread */
  .section-title { color: var(--navy); font-weight: 900; font-size: 24px; line-height: 1.1; }
  .tutors-title { left: 36px; top: 318px; }
  .students-title { left: 662px; top: 34px; }
  .point-list { list-style: disc; padding-left: 16px; font-size: 12px; line-height: 1.4; }
  .tutors-list { left: 40px; top: 350px; width: 290px; }
  .students-list { left: 664px; top: 68px; width: 172px; font-size: 10.5px; }
  .point-list ul { list-style: disc; padding-left: 14px; }
  .tutors-slogan { left: 36px; top: 462px; width: 250px;
    color: var(--navy); font-weight: 900; font-size: 22px; line-height: 1.1; }
  .students-slogan { left: 660px; top: 222px; width: 172px; text-align: center;
    color: var(--navy); font-weight: 900; font-size: 18px; line-height: 1.15; }
</style>
</head>
<body>

<section class="spread spread--outside">
  <svg class="spread__art" viewBox="0 0 840 560" width="840" height="560">
    <defs>
      <linearGradient id="outsideBlue" x1="0" y1="0" x2="1" y2="1">
        <stop offset="0" stop-color="#2ab0e4"/>
        <stop offset="1" stop-color="#0f74bd"/>
      </linearGradient>
      <linearGradient id="photoPresenter" x1="0" y1="0" x2="0" y2="1">
        <stop offset="0" stop-color="#eceeef"/>
        <stop offset=".6" stop-color="#d8dadb"/>
        <stop offset="1" stop-color="#9a9ea3"/>
      </linearGradient>
      <linearGradient id="photoGroup" x1="0" y1="0" x2="1" y2="1">
        <stop offset="0" stop-color="#d9c7b8"/>
        <stop offset=".5" stop-color="#9fb6d2"/>
        <stop offset="1" stop-color="#e6e0da"/>
      </linearGradient>
    </defs>
    <rect width="840" height="560" fill="url(#outsideBlue)"/>
    <path d="M0,12 L300,12 C255,180 330,390 300,548 L0,548 Z" fill="url(#photoPresenter)"
          role="img" aria-label="Photo of a tutor presenting at a whiteboard"/>
    <path d="M300,12 C255,180 330,390 300,548" fill="none" stroke="var(--navy)" stroke-width="6"/>
    <path d="M460,548 C480,400 580,330 840,300 L840,548 Z" fill="url(#photoGroup)"
          role="img" aria-label="Photo of adult learners and tutors working together at a table"/>
    <path d="M460,548 C480,400 580,330 840,300" fill="none" stroke="var(--navy)" stroke-width="6"/>
    <rect x="0" y="0" width="840" height="12" fill="var(--navy)"/>
    <rect x="0" y="548" width="840" height="12" fill="var(--navy)"/>
  </svg>

  <h2 class="txt cta-title">Don’t waste a moment!</h2>
  <p class="txt cta-sub">Contact us today to learn more.</p>
  <p class="txt contact-line contact-line--desk">Volunteer Desk: <strong>555-014-2280</strong></p>
  <p class="txt contact-line contact-line--branches">Cedar Glen, Millbrook &amp; Harbor Point: <strong>555-017-3904</strong></p>
  <p class="txt contact-line contact-line--email">email: reading@examplelibrary.org</p>

  <div class="logo-badge" style="left:385px; top:385px; width:112px; height:112px;">
    <span class="logo-badge__name">Reading<br>Bridge<br>Friends</span>
  </div>

  <div class="logo-badge" style="left:640px; top:-20px; width:130px; height:130px;">
    <span class="logo-badge__name" style="padding-top:16px;">Reading<br>Bridge<br>Friends</span>
  </div>
  <h1 class="txt cover-title">VOLUNTEER</h1>
  <p class="txt cover-tag">Enrich a Life!</p>
  <p class="txt cover-lede">Help an adult learn to read, write or speak English</p>
</section>

<section class="spread spread--inside">
  <svg class="spread__art" viewBox="0 0 840 560" width="840" height="560">
    <defs>
      <linearGradient id="insideBlue" x1="0" y1="0" x2="1" y2="1">
        <stop offset="0" stop-color="#2ab0e4"/>
        <stop offset="1" stop-color="#1080c6"/>
      </linearGradient>
      <linearGradient id="photoClass" x1="0" y1="0" x2="1" y2="1">
        <stop offset="0" stop-color="#ecebe8"/>
        <stop offset=".5" stop-color="#c9bfb6"/>
        <stop offset="1" stop-color="#e9e9e9"/>
      </linearGradient>
      <linearGradient id="photoPair" x1="0" y1="0" x2="1" y2="0">
        <stop offset="0" stop-color="#7f97b8"/>
        <stop offset=".5" stop-color="#d9c2b0"/>
        <stop offset="1" stop-color="#5f7a5a"/>
      </linearGradient>
    </defs>
    <rect width="840" height="560" fill="url(#insideBlue)"/>
    <path d="M0,0 L645,0 L645,90 C570,220 430,250 270,256 C160,262 60,280 0,302 Z" fill="url(#photoClass)"
          role="img" aria-label="Photo of a teacher speaking to a class of adult students"/>
    <path d="M645,90 C570,220 430,250 270,256 C160,262 60,280 0,302" fill="none" stroke="var(--navy)" stroke-width="6"/>
    <path d="M320,560 C370,430 480,385 620,372 C720,362 800,332 840,305 L840,560 Z" fill="url(#photoPair)"
          role="img" aria-label="Photo of an older man and woman studying together at a laptop"/>
    <path d="M320,560 C370,430 480,385 620,372 C720,362 800,332 840,305" fill="none" stroke="var(--navy)" stroke-width="6"/>
  </svg>

  <h2 class="txt section-title students-title">Students</h2>
  <ul class="txt point-list students-list">
    <li>Students are adults in need of
      <ul>
        <li>basic literacy skills</li>
        <li>pre-GED skills</li>
        <li>conversational English</li>
      </ul>
    </li>
    <li>Tutoring is free of charge</li>
    <li>Tutoring is one-on-one</li>
    <li>Flexible scheduling during library hours</li>
    <li>Lessons focus on student goals</li>
  </ul>
  <p class="txt students-slogan">If you can read, you can tutor!</p>

  <div class="logo-badge" style="left:400px; top:244px; width:116px; height:116px;">
    <span class="logo-badge__name">Reading<br>Bridge<br>Friends</span>
  </div>

  <h2 class="txt section-title tutors-title">Tutors</h2>
  <ul class="txt point-list tutors-list">
    <li>No special skills or degrees needed — just a degree of caring!</li>
    <li>Training offered throughout the year</li>
    <li>Tutors meet students weekly at a library</li>
    <li>Instructional materials provided</li>
    <li>Ongoing support available</li>
  </ul>
  <p class="txt tutors-slogan">Teach an adult to read and you’ll change a life forever.</p>
</section>

</body>
</html>
```